VOMRA Pty Ltd Business Card

Looking for a simple yet eye-catching double-sided business card design using my company logo on one side and contact details on the other.

Target Market(s)

Government

Industry/Entity Type

Communication Systems Engineering

Contact Information for Business Card

VOMRA Pty Ltd

Requirements
Nice to have
• Would be great to have a QR code so details can be scanned into contacts

```html
<!DOCTYPE html>
<html lang="en">
<head>
<meta charset="utf-8">
<title>VOMRA Pty Ltd Business Card</title>
<link href="https://fonts.googleapis.com/css2?family=Open+Sans:wght@400;600;700&display=swap" rel="stylesheet">
<style>
  :root {
    --slate: #333e46;
    --slate-deep: #1f272c;
    --paper: #ffffff;
    --ink: #1d2226;
    --backdrop: #e9e9e7;
  }
  * { box-sizing: border-box; margin: 0; padding: 0; }
  html, body { width: 1200px; height: 780px; overflow: hidden; }
  body {
    background: var(--backdrop);
    font-family: "Open Sans", Arial, sans-serif;
    color: var(--ink);
    position: relative;
  }
  .card {
    position: absolute;
    top: 230px;
    width: 520px;
    height: 310px;
    border-radius: 22px;
    overflow: hidden;
    box-shadow: 0 6px 18px rgba(0,0,0,0.18);
  }
  .card--front { left: 50px; background: var(--paper); }
  .card--back { left: 630px; background: var(--slate); }

  .wave { position: absolute; inset: 0; width: 100%; height: 100%; }

  .brand {
    position: absolute;
    display: flex;
    align-items: center;
    gap: 12px;
  }
  .brand__mark { width: 26px; height: 26px; border-radius: 50%; }
  .brand__name { font-weight: 700; letter-spacing: 2px; line-height: 1; }

  .card--front .brand { top: 30px; left: 48px; }
  .card--front .brand__mark { background: var(--slate); }
  .card--front .brand__name { font-size: 52px; color: var(--slate); }

  .contact {
    position: absolute;
    top: 104px;
    left: 50px;
    font-size: 14px;
    line-height: 1.45;
    color: var(--ink);
  }
  .contact__address { margin-bottom: 6px; }
  .contact__row { display: flex; align-items: center; gap: 8px; }
  .contact__icon { width: 12px; height: 12px; flex: none; }

  .person {
    position: absolute;
    top: 148px;
    right: 34px;
    text-align: right;
  }
  .person__name { font-size: 30px; font-weight: 700; color: var(--slate); line-height: 1.1; }
  .person__title { font-size: 16px; font-weight: 600; color: var(--ink); }

  .card--back .brand {
    top: 50%; left: 50%;
    transform: translate(-50%, -50%);
    gap: 16px;
  }
  .card--back .brand__mark { width: 34px; height: 34px; background: var(--slate-deep); }
  .card--back .brand__name { font-size: 72px; color: var(--slate-deep); }
</style>
</head>
<body>

<section class="card card--front" aria-label="Business card front">
  <svg class="wave" viewBox="0 0 520 310" preserveAspectRatio="none" aria-hidden="true">
    <path d="M0 150 C8 215 60 252 150 264 C260 278 400 252 520 240 L520 310 L0 310 Z" fill="var(--slate)"/>
    <path d="M0 118 C10 190 56 232 140 252" stroke="var(--slate)" stroke-width="3" fill="none"/>
  </svg>

  <div class="brand">
    <span class="brand__mark"></span>
    <span class="brand__name">VOMRA</span>
  </div>

  <div class="contact">
    <p class="contact__address">45-47 Harbour Lane Redfern<br>NSW 2016 Australia</p>
    <p class="contact__row">
      <svg class="contact__icon" viewBox="0 0 12 12" aria-hidden="true"><path d="M2.5 1 L4.5 1 L5.2 3.6 L4 4.6 C4.7 6 5.9 7.3 7.4 8 L8.4 6.8 L11 7.5 L11 9.5 C11 10.4 10.3 11 9.4 11 C5 10.6 1.4 7 1 2.6 C1 1.7 1.6 1 2.5 1 Z" fill="var(--ink)"/></svg>
      (555) 214-6630
    </p>
    <p class="contact__row">
      <svg class="contact__icon" viewBox="0 0 12 12" aria-hidden="true"><circle cx="6" cy="6" r="5" fill="none" stroke="var(--ink)" stroke-width="1.3"/><path d="M1 6 H11 M6 1 C3.5 4 3.5 8 6 11 M6 1 C8.5 4 8.5 8 6 11" stroke="var(--ink)" stroke-width="1" fill="none"/></svg>
      www.vomra.com.au
    </p>
    <p class="contact__row">
      <svg class="contact__icon" viewBox="0 0 12 12" aria-hidden="true"><rect x="0.8" y="2.2" width="10.4" height="7.6" rx="1" fill="none" stroke="var(--ink)" stroke-width="1.3"/><path d="M1 2.6 L6 6.6 L11 2.6" stroke="var(--ink)" stroke-width="1.2" fill="none"/></svg>
      admin@vomra.com.au
    </p>
  </div>

  <div class="person">
    <p class="person__name">Daniel Hartley</p>
    <p class="person__title">Co-Founder</p>
  </div>
</section>

<section class="card card--back" aria-label="Business card back">
  <div class="brand">
    <span class="brand__mark"></span>
    <span class="brand__name">VOMRA</span>
  </div>
</section>

</body>
</html>
```